KORV PTY LTD - Business Cards

Design a modern business card - using the attached Designs.
Same design as on the front, apart from the names/numbers/emails to be different.
We want the cards to be very glossy to stand out, do I think the simple black/white/metallic will be effective.
Both lots of details below:

Tom Wrenshaw
Director
tom_korv@nulvane.com
0438 274 093

Lewis Corbyn
Director
lewis_korv@nulvane.com
0419 385 642

Industry/Entity Type

Business

```html
<!DOCTYPE html>
<html lang="en">
<head>
<meta charset="utf-8">
<title>KORV PTY LTD – Business Cards</title>
<link rel="stylesheet" href="https://fonts.googleapis.com/css2?family=Ubuntu:wght@400;700&display=swap">
<style>
  :root {
    --stage: #e9e7e4;
    --card-light: #ffffff;
    --card-shade: #eceded;
    --ink: #1f1f1f;
    --ink-soft: #4a4a4a;
    --metal-dark: #2c2c2c;
    --metal-mid: #8a8a8a;
    --rule: #c9c9c9;
  }
  html, body {
    margin: 0;
    width: 1200px;
    height: 913px;
    overflow: hidden;
    background: var(--stage);
    font-family: "Ubuntu", Arial, sans-serif;
  }
  .stage {
    position: relative;
    width: 1200px;
    height: 913px;
  }
  .card {
    position: absolute;
    width: 520px;
    height: 297px;
    background: linear-gradient(135deg, var(--card-light) 0%, var(--card-shade) 55%, var(--card-light) 100%);
    border-radius: 4px;
    box-shadow: 0 10px 30px rgba(0,0,0,0.18), 0 2px 4px rgba(0,0,0,0.12);
    overflow: hidden;
  }
  .card--front { left: 50px; top: 150px; }
  .card--back  { left: 630px; top: 466px; }

  .brand {
    position: absolute;
    display: flex;
    align-items: center;
    gap: 16px;
    color: var(--metal-dark);
    font-weight: 700;
    letter-spacing: 4px;
  }
  .brand__dot {
    border-radius: 50%;
    background: var(--metal-mid);
  }
  .card--front .brand {
    left: 50%; top: 50%;
    transform: translate(-50%, -50%);
    font-size: 76px;
  }
  .card--front .brand__dot { width: 64px; height: 64px; }

  .card--back .brand {
    left: 36px; top: 50%;
    transform: translateY(-50%);
    font-size: 38px;
    gap: 10px;
    letter-spacing: 2px;
  }
  .card--back .brand__dot { width: 32px; height: 32px; }

  .bracket {
    position: absolute;
    left: 218px;
    top: 40px;
    width: 16px;
    height: 217px;
  }

  .contacts {
    position: absolute;
    left: 258px;
    top: 36px;
    color: var(--ink);
  }
  .person { margin-bottom: 26px; }
  .person__name {
    font-size: 20px;
    font-weight: 700;
    margin: 0;
    color: var(--ink-soft);
  }
  .person__role {
    font-size: 11px;
    margin: 1px 0 6px;
    color: var(--ink-soft);
  }
  .person__line {
    display: flex;
    align-items: center;
    gap: 12px;
    font-size: 16px;
    margin: 2px 0;
    color: var(--ink);
  }
  .icon { width: 16px; height: 14px; flex: none; }
</style>
</head>
<body>
<main class="stage">

  <section class="card card--front" aria-label="Card front">
    <div class="brand">
      <span class="brand__dot"></span>
      <span class="brand__name">KORV</span>
    </div>
  </section>

  <section class="card card--back" aria-label="Card back">
    <div class="brand">
      <span class="brand__dot"></span>
      <span class="brand__name">KORV</span>
    </div>

    <svg class="bracket" viewBox="0 0 16 217" aria-hidden="true">
      <path d="M1 1 H6 V100 L14 108 L6 116 V216 H1" fill="none" stroke="var(--rule)" stroke-width="1.5"/>
    </svg>

    <div class="contacts">
      <div class="person">
        <p class="person__name">Tom Wrenshaw</p>
        <p class="person__role">Director</p>
        <p class="person__line">
          <svg class="icon" viewBox="0 0 16 14" aria-hidden="true"><path d="M1 4 Q8 -1 15 4 L13 6 L11 4.5 H5 L3 6 Z M4 7 H12 L14 13 H2 Z" fill="var(--ink)"/></svg>
          0438 274 093
        </p>
        <p class="person__line">
          <svg class="icon" viewBox="0 0 16 14" aria-hidden="true"><rect x="1" y="2" width="14" height="10" fill="var(--ink)"/><path d="M1 2 L8 8 L15 2" fill="none" stroke="#fff" stroke-width="1.2"/></svg>
          tom_korv@nulvane.com
        </p>
      </div>
      <div class="person">
        <p class="person__name">Lewis Corbyn</p>
        <p class="person__role">Director</p>
        <p class="person__line">
          <svg class="icon" viewBox="0 0 16 14" aria-hidden="true"><path d="M1 4 Q8 -1 15 4 L13 6 L11 4.5 H5 L3 6 Z M4 7 H12 L14 13 H2 Z" fill="var(--ink)"/></svg>
          0419 385 642
        </p>
        <p class="person__line">
          <svg class="icon" viewBox="0 0 16 14" aria-hidden="true"><rect x="1" y="2" width="14" height="10" fill="var(--ink)"/><path d="M1 2 L8 8 L15 2" fill="none" stroke="#fff" stroke-width="1.2"/></svg>
          lewis_korv@nulvane.com
        </p>
      </div>
    </div>
  </section>

</main>
</body>
</html>
```